NZ First of it's kind solutions directory and marketplace for busy Mums needs a business card design

We need a business card design for our new nationwide business in NZ (long term plans to go global). We provide solutions to the everyday challenges that busy Mums face by connecting them with quality communities and suppliers of carefully selected, relevant products and services. We sell direct via our online marketplace. The final design should communicate our values of inclusivity, quality and smart solutions. Colours should incorporate our logo colour palette of #477077 and #6ba8b2. Our website is at https://www.brightnestmums.example

Target Market(s)

busy Mums, Age 28 – 50, female, income over $100K, location main centres NZ primarily but NZ wide. Is likely juggling work or career with a young family. Probably had hobbies which have fallen by the wayside.
-Wants to succeed in her chosen career without compromising on family life
-to successfully juggle her career without feeling like she is compromising her children
- Is time poor, something always has to give and it’s generally her health (she’ll stay up late, get stressed)
- probably ex corporate or professional career. Has discretional income

Industry/Entity Type

Business

Contact Information for Business Card

Lena Forbisher, Founder, BrightNestMums.example (Strapline Tap; Gather; Sorted), 47 Kowhai Terrace, Ellerslie, Auckland 1051, New Zealand. Mob: 021 483 517 Ph: +64 (0)9 571 4860

Font styles to use
Other font styles liked:
• Raleway, and/or Architects Daughter

Colors
00a990
33b8a4
86cfc6
cfeae6

Requirements
Must have
• the above details, streamline. the logo and colours associated with those logos
Should not have
• foil or metallic colours

```html
<!DOCTYPE html>
<html lang="en">
<head>
<meta charset="utf-8">
<title>BrightNestMums Business Card</title>
<link rel="stylesheet" href="https://fonts.googleapis.com/css2?family=Raleway:wght@400;500;700;800&display=swap">
<style>
  :root {
    --teal: #00a98f;
    --white: #ffffff;
    --mint: #cfeae6;
    --backdrop: #e4e4e2;
  }
  html, body {
    margin: 0;
    padding: 0;
    width: 1200px;
    height: 1000px;
    overflow: hidden;
    background: var(--backdrop);
    font-family: "Raleway", sans-serif;
  }
  .canvas { position: relative; width: 1200px; height: 1000px; }

  /* Front of card */
  .card-front {
    position: absolute; left: 150px; top: 100px;
    width: 630px; height: 360px;
    background: var(--white);
    border-radius: 40px;
    box-shadow: 0 6px 14px rgba(0,0,0,0.25);
  }
  .card-front .panel {
    position: absolute; left: 30px; top: 30px;
    width: 573px; height: 302px;
    background: var(--teal);
    border-radius: 30px;
  }
  .brand {
    position: absolute;
    display: flex; align-items: center;
    color: var(--white);
    font-weight: 800;
    white-space: nowrap;
  }
  .brand .dot {
    border-radius: 50%;
    background: var(--mint);
    flex: none;
  }
  .card-front .brand { left: 96px; top: 118px; font-size: 46px; letter-spacing: -0.5px; }
  .card-front .brand .dot { width: 40px; height: 40px; margin-right: 20px; }

  /* Back of card */
  .card-back {
    position: absolute; left: 373px; top: 547px;
    width: 634px; height: 362px;
    background: var(--teal);
    border-radius: 36px;
    overflow: hidden;
    box-shadow: 0 6px 14px rgba(0,0,0,0.25);
    color: var(--white);
  }
  .person-name {
    position: absolute; left: 47px; top: 72px;
    font-size: 28px; font-weight: 400; margin: 0;
  }
  .person-role {
    position: absolute; left: 47px; top: 114px;
    font-size: 19px; font-weight: 500; margin: 0;
  }
  .card-back .brand { left: 358px; top: 84px; font-size: 26px; letter-spacing: -0.3px; }
  .card-back .brand .dot { width: 26px; height: 26px; margin-right: 10px; }

  .address-band { position: absolute; left: 0; top: 173px; width: 634px; height: 30px; }
  .address {
    position: absolute; left: 134px; top: 179px;
    font-size: 16.5px; font-weight: 500; color: var(--teal);
    margin: 0; white-space: nowrap;
  }

  .contact-list { position: absolute; left: 44px; top: 222px; margin: 0; padding: 0; list-style: none; }
  .contact-list li {
    display: flex; align-items: center;
    height: 35px; font-size: 19px; font-weight: 500;
    white-space: nowrap;
  }
  .contact-list svg { width: 24px; height: 24px; margin-right: 16px; flex: none; }
  .strapline { font-size: 14px; margin-left: 6px; }
</style>
</head>
<body>
<div class="canvas">

  <section class="card-front">
    <div class="panel">
      <div class="brand"><span class="dot"></span>BrightNestMums</div>
    </div>
  </section>

  <section class="card-back">
    <h1 class="person-name">Lena Forbisher</h1>
    <p class="person-role">Founder</p>
    <div class="brand"><span class="dot"></span>BrightNestMums</div>

    <svg class="address-band" viewBox="0 0 634 30" aria-hidden="true">
      <rect x="0" y="0" width="634" height="2" fill="#ffffff"/>
      <path d="M108 0 H634 V27 H118 Q112 27 111 21 Z" fill="#ffffff"/>
    </svg>
    <p class="address">47 Kowhai Terrace, Ellerslie, Auckland 1051, New Zealand</p>

    <ul class="contact-list">
      <li>
        <svg viewBox="0 0 24 24" aria-hidden="true" fill="#ffffff">
          <path d="M2 7c0-2 2-3 10-3s10 1 10 3v2h-5V7.5c-1-.5-3-.7-5-.7s-4 .2-5 .7V9H2z"/>
          <path d="M5 11h14l1 9H4z"/>
          <circle cx="12" cy="15.5" r="2.6" fill="#00a98f"/>
        </svg>
        +64 (0)9 571 4860
      </li>
      <li>
        <svg viewBox="0 0 24 24" aria-hidden="true" fill="#ffffff">
          <path d="M6.6 3.5l3 3.3-1.8 2.4c1 2.3 2.8 4.1 5 5.1l2.4-1.8 3.3 3-1.7 3C11 18 6 13 3.5 5.3z"/>
        </svg>
        021 483 517
      </li>
      <li>
        <svg viewBox="0 0 24 24" aria-hidden="true" fill="none" stroke="#ffffff" stroke-width="1.8">
          <circle cx="12" cy="12" r="9"/>
          <ellipse cx="12" cy="12" rx="4" ry="9"/>
          <path d="M3 12h18M5 7h14M5 17h14"/>
        </svg>
        www.brightnestmums.example<span class="strapline">( Strapline Tap; Gather; Sorted )</span>
      </li>
    </ul>
  </section>

</div>
</body>
</html>
```